Whirlwind Mabel Launching in New Location

I need a marketing postcard that announces the opening of Whirlwind Mabel! It should grab the attention of the target market by highlighting the services they could use the most. I want them to look at this postcard and say, "Oh my god, I totally need this!" Whirlwind Mabel is all about putting time back in the lives of busy working people by taking every day tasks off their "to do" lists.

If using pictures, I'd like a more retro look and feel. Whirlwind Mabel reminds me of the 50' and 60's. Parents and families juggling multiple tasks at once... see pic examples

Details:
Whirlwind Mabel open for business in Mercer County starting August 4, 2014. Taking reservations now!

What we can do to save YOU time:
Grocery Shopping
Gift Shopping, wrapping and shipping
General Errands
Travel Arrangements and Event Planning
Project Management and Organization

What YOU can do with the time YOU save:
Spend time with your kids, family and friends
Relax and enjoy life!

Grand Opening special - Buy 2 hours, get 1 free! *****I don't know if I will use this, what do you think?******

```html
<!DOCTYPE html>
<html lang="en">
<head>
<meta charset="utf-8">
<title>Whirlwind Mabel – Grand Opening Postcard</title>
<link rel="stylesheet" href="https://fonts.googleapis.com/css2?family=Fira+Sans:wght@400;500;600&family=Dancing+Script:wght@400&display=swap">
<style>
  :root {
    --paper: #ffffff;
    --mint: #d4e9dd;
    --sage: #6fa98c;
    --rose: #e8557b;
    --ink: #4b4847;
    --art-warm: #f3d9b6;
    --art-green: #cfe0bf;
  }
  * { margin: 0; padding: 0; box-sizing: border-box; }
  html, body { width: 1200px; height: 800px; overflow: hidden; background: var(--paper); }
  .postcard {
    position: relative;
    width: 1200px;
    height: 800px;
    background: var(--paper);
    font-family: "Fira Sans", sans-serif;
    color: var(--ink);
  }
  .hero-art {
    position: absolute;
    left: 50px;
    top: 40px;
    width: 400px;
    height: 720px;
    background:
      radial-gradient(ellipse at 48% 45%, rgba(229,83,47,0.55) 0 14%, transparent 30%),
      linear-gradient(135deg, var(--art-green) 0%, var(--art-warm) 55%, #cfe4dc 100%);
  }
  .offer-panel {
    position: absolute;
    left: 652px;
    top: 24px;
    width: 502px;
    height: 600px;
    background: var(--mint);
    text-align: center;
  }
  .brand-name {
    margin-top: 66px;
    font-size: 44px;
    line-height: 53px;
    font-weight: 600;
    color: var(--sage);
    letter-spacing: 1px;
    text-transform: uppercase;
  }
  .tagline {
    margin-top: 26px;
    font-family: "Dancing Script", cursive;
    font-size: 28px;
    line-height: 34px;
    color: var(--rose);
  }
  .special {
    margin-top: 48px;
    font-size: 36px;
    font-weight: 600;
    line-height: 46px;
    color: var(--sage);
    font-variant: small-caps;
    letter-spacing: 0.5px;
  }
  .launch {
    margin-top: 46px;
    font-size: 31px;
    font-weight: 500;
    line-height: 42px;
    color: var(--rose);
  }
  .reservations {
    position: absolute;
    right: 430px;
    top: 679px;
    text-align right;
    text-align: right;
    font-size: 35px;
    font-weight: 500;
    line-height: 42px;
    color: var(--ink);
  }
  .contact {
    position: absolute;
    left: 804px;
    top: 679px;
    list-style: none;
    color: var(--ink);
  }
  .contact li { display: flex; align-items: center; gap: 16px; height: 42px; }
  .contact svg { flex: none; }
  .contact-phone { font-size: 40px; font-weight: 600; }
  .contact-email { font-size: 23px; font-weight: 600; font-variant: small-caps; letter-spacing: 0.5px; }
</style>
</head>
<body>
  <main class="postcard">
    <div class="hero-art" role="img" aria-label="Retro illustration of a busy woman in a red coat juggling shopping bags, a briefcase, a piggy bank, papers and a baby stroller"></div>

    <section class="offer-panel">
      <h1 class="brand-name">Whirlwind Mabel</h1>
      <p class="tagline">“We whirl around so you don’t have to!”</p>
      <p class="special">Grand Opening Special:<br>Buy 2 Hours, Get 1 Free!</p>
      <p class="launch">Whirlwind Mabel Open For<br>Business In<br>Mercer County Starting<br>August 4, 2014.</p>
    </section>

    <p class="reservations">Taking<br>Reservations Now!</p>

    <ul class="contact">
      <li class="contact-phone">
        <svg width="26" height="22" viewBox="0 0 24 20" aria-hidden="true">
          <path d="M2 7c0-3 4-5 10-5s10 2 10 5v2h-5V7H7v2H2z" fill="var(--ink)"/>
          <path d="M5 10h14l3 8H2z" fill="var(--ink)"/>
          <circle cx="12" cy="14" r="2.4" fill="var(--paper)"/>
        </svg>
        724-555-0143
      </li>
      <li class="contact-email">
        <svg width="26" height="17" viewBox="0 0 24 16" aria-hidden="true">
          <rect x="0" y="0" width="24" height="16" fill="var(--ink)"/>
          <path d="M1 1l11 8 11-8" fill="none" stroke="var(--paper)" stroke-width="1.6"/>
        </svg>
        mabel@whirlwindmabel.biz
      </li>
    </ul>
  </main>
</body>
</html>
```